Webdesign für Bedrucken Papiertaschen, Schildern etc.
Zielgruppe
Wir bedrucken Papiertaschen, Papierbeutel, Laternen, Aluplaketten, Schilder, etc. und lasern Hundemarken. Zielgruppen von Privat bis Geschäftskunden
Aufgabenstellung
Der Shop sollte ein einfacher und kostengünstiger 'web2print'-shop werden. Wo die Kunden anhand von einem Editor Ihre Logos oder Druckvorlagen selber hochladen und/oder gestalten könne. Bisher haben die Kunden eifach ihre Bidldatei per E-Mail geschickt und wir haben diese dann weiter verarbeit.
Der Shop sollte, wenn möglich, günstig im Unterhalt sein, da wir nicht abschätzen können, wie gut diese laufen wird.
Wir haben wie 3 Bereich: 1. Papierbeutel/Taschen / 2. Stallplaketten (für z.B. Pferdesport) / 3. Diverses (Wie z.B. die Laternen, Schilder, Hundemarken, etc.)
Es würde sich um eine separate Webseite handeln. Daher ist bei Design freie Hand, eifach und klar... auch für nicht so ambitionierte Privatkunden oder kleine Unternehmen.

```html
<!DOCTYPE html>
<html lang="de">
<head>
<meta charset="utf-8">
<title>Tütenwerk – Individuell bedruckt</title>
<link href="https://fonts.googleapis.com/css2?family=Outfit:wght@400;500;600;700&family=Poppins:wght@400;500;600&display=swap" rel="stylesheet">
<style>
:root{
  --pink:#ff3d8b;
  --purple:#7b3ff2;
  --violet:#a24df0;
  --ink:#15131c;
  --muted:#7a7886;
  --line:#e7e5ee;
  --soft:#f5f4f8;
  --orange:#ff4a1c;
  --white:#fff;
  --grad:linear-gradient(90deg,var(--pink),var(--purple));
}
*{box-sizing:border-box;margin:0;padding:0}
html,body{width:1200px;height:3941px;overflow:hidden}
body{font-family:"Poppins",sans-serif;color:var(--ink);background:#fff;position:relative;font-size:11px}
h1,h2,h3,h4{font-family:"Outfit",sans-serif;font-weight:500}
.wrap{position:absolute;left:0;width:1200px}
.ph{position:absolute;border-radius:4px}
.tag{display:inline-block;font-size:9px;color:var(--pink);border:1px solid #f3d6e4;border-radius:20px;padding:3px 12px;background:#fff}
.uline{background:linear-gradient(var(--purple),var(--purple)) no-repeat 0 100%/100% 2px}
.check{display:flex;align-items:center;gap:8px;font-size:10px;color:#444;margin-bottom:10px;white-space:nowrap}
.check i{flex:none;width:11px;height:11px;border-radius:50%;background:var(--purple);display:inline-flex;align-items:center;justify-content:center}
.check i::after{content:"";width:4px;height:2px;border-left:1.5px solid #fff;border-bottom:1.5px solid #fff;transform:rotate(-45deg) translate(0,-1px)}
.btn-grad{display:inline-block;background:var(--grad);color:#fff;border-radius:22px;font-size:10px;padding:12px 20px;white-space:nowrap}

/* top bar */
.topbar{top:0;height:23px;background:var(--grad);color:#fff;font-size:10px;display:flex;align-items:center;padding:0 122px;gap:22px}
.topbar .right{margin-left:auto}
/* nav */
.nav{top:23px;height:57px;border-bottom:1px solid var(--line);display:flex;align-items:center;padding:0 122px}
.logo{position:absolute;left:122px;top:23px;width:98px;height:83px;background:var(--purple);display:flex;align-items:center;justify-content:center;color:#fff;font-family:"Outfit",sans-serif;font-weight:700;font-size:17px;z-index:3}
.menu{display:flex;gap:40px;margin-left:280px;font-size:10px;white-space:nowrap}
.nav .acts{margin-left:auto;display:flex;gap:9px;align-items:center;white-space:nowrap}
.pill{font-size:8.5px;border-radius:18px;padding:9px 14px;white-space:nowrap}
.pill.fill{background:var(--pink);color:#fff}
.pill.out{border:1.5px solid var(--ink);padding:8px 13px}
/* hero */
.hero{top:80px;height:522px;overflow:hidden}
.hero-bg{left:0;top:0;width:1200px;height:522px;border-radius:0;background:linear-gradient(100deg,#c9a88a 0%,#e6d3bf 45%,#f2e9df 70%,#e8dccd 100%)}
.hero-prod{left:540px;top:200px;width:660px;height:322px;border-radius:0;background:linear-gradient(90deg,rgba(180,130,80,.25),rgba(240,235,230,.55) 50%,rgba(200,170,140,.3))}
.hero-blob{position:absolute;left:60px;top:40px}
.hero-txt{position:absolute;left:158px;top:135px;color:#fff}
.hero-txt .tag{background:rgba(255,255,255,.25);border:none;color:#fff}
.hero-txt h1{font-size:60px;line-height:64px;font-weight:600;margin-top:10px}
.hero-txt p{font-size:11px;line-height:18px;margin-top:8px}
.hero-btns{margin-top:22px;display:flex;gap:10px}
.hero-btns span{background:#fff;color:var(--ink);border-radius:20px;padding:12px 44px;font-size:10px;white-space:nowrap}
.notch{position:absolute;left:540px;top:482px;width:120px;height:40px;background:#fff;border-radius:60px 60px 0 0;text-align:center;font-size:8px;padding-top:20px;color:#555}
/* features */
.features{top:602px;left:190px;width:818px;height:92px;background:#fff;box-shadow:0 8px 24px rgba(40,20,80,.08);display:flex;align-items:center;justify-content:space-around;padding:0 20px}
.feat{display:flex;gap:10px;align-items:center;white-space:nowrap}
.feat b{display:block;font-size:10px;font-weight:500}
.feat small{font-size:8.5px;color:var(--muted)}
/* services */
.serv{top:735px;height:497px}
.serv .img1{left:156px;top:20px;width:290px;height:260px;background:linear-gradient(160deg,#ece7f3,#c9a77f)}
.serv .img2{left:313px;top:112px;width:276px;height:336px;background:linear-gradient(160deg,#eee7dc,#c99a63 60%,#e9e4dd);border:6px solid #fff}
.serv .blob{position:absolute;left:1100px;top:230px;width:140px;height:240px;border-radius:50%;background:radial-gradient(#fbe5f3,#fff0)}
.serv .txt{position:absolute;left:638px;top:62px;width:440px}
.serv h2{font-size:34px;line-height:40px;margin-top:14px}
.serv p{font-size:9.5px;color:var(--muted);line-height:17px;border-left:1px solid var(--line);padding-left:10px;margin:24px 0 22px}
.swiss{position:absolute;left:215px;top:200px;border-left:2px solid var(--pink);padding:12px 0 12px 14px;font-size:14px;white-space:nowrap}
.swiss b{color:var(--pink);font-size:20px;font-family:"Outfit",sans-serif;font-weight:600;margin-right:4px}
.dot{position:absolute;border-radius:50%}
/* products */
.prod{top:1232px;height:520px;background:var(--soft);text-align:center}
.prod .tag{margin-top:20px}
.prod h2{font-size:34px;margin-top:12px}
.cards{display:flex;gap:18px;justify-content:center;margin-top:18px}
.card{width:306px;height:358px;background:#fff;position:relative;padding:18px}
.card .ph{position:relative;width:270px;height:238px;border-radius:0}
.card h3{font-size:14px;font-weight:600;margin-top:22px}
.card p{font-size:9px;color:var(--muted);margin-top:10px}
.card a{display:inline-block;margin-top:10px;font-size:9.5px;color:var(--ink);text-decoration:underline}
/* steps */
.steps{top:1806px;height:250px;text-align:center}
.steps h2{font-size:34px;line-height:38px;margin-top:14px}
.steprow{position:absolute;left:122px;top:145px;width:956px;display:flex;justify-content:space-between}
.step{text-align:center;font-size:12px;font-weight:600;font-family:"Outfit",sans-serif;white-space:nowrap}
.step svg{display:block;margin:0 auto 10px}
/* why */
.why{top:2097px;height:400px}
.why .txt{position:absolute;left:122px;top:40px;width:480px}
.why h2{font-size:34px;margin-top:12px}
.why p{font-size:9.5px;color:var(--muted);line-height:17px;border-left:1px solid var(--line);padding-left:8px;margin:24px 0 20px}
.grid2{display:grid;grid-template-columns:190px 260px;column-gap:0}
.grid2 .check{font-size:9px;margin-bottom:14px}
.why .c1{left:645px;top:14px;width:165px;height:198px;background:linear-gradient(160deg,#2a77a8,#c25a27 60%,#1d2b3a)}
.why .c2{left:734px;top:144px;width:165px;height:235px;background:linear-gradient(170deg,#3a3537,#e8631a 45%,#9aa0a5)}
.why .c3{left:908px;top:65px;width:148px;height:198px;background:linear-gradient(160deg,#cfd2d4,#e7e0d4 55%,#c8c4bd)}
/* gallery */
.gal{top:2540px;height:600px}
.gal h3{text-align:center;font-size:22px;line-height:32px;font-weight:400}
.gal .ph{border-radius:0}
.gal .btn{position:absolute;left:512px;top:470px;width:178px;height:40px;border-radius:22px;background:#fff;box-shadow:2px 3px 0 var(--purple),0 4px 10px rgba(0,0,0,.08);font-size:9px;display:flex;align-items:center;justify-content:center;white-space:nowrap}
/* testimonials */
.test{top:3213px;height:450px}
.test h2{position:absolute;left:122px;top:45px;font-size:34px}
.test .tag{position:absolute;left:122px;top:0}
.arrows{position:absolute;left:1000px;top:50px;display:flex;gap:12px}
.arrows span{width:30px;height:30px;display:flex;align-items:center;justify-content:center}
.portrait{position:absolute;left:198px;top:105px;width:285px;height:285px;border-radius:50%;background:radial-gradient(circle at 50% 40%,#d8c6b6,#a89384 70%,#8e7b70)}
.avatar{position:absolute;border-radius:50%;border:3px solid #fff;box-shadow:0 3px 10px rgba(0,0,0,.12)}
.quote{position:absolute;left:522px;top:130px;width:550px}
.quote .head{display:flex;gap:18px;align-items:flex-start}
.quote .head b{font-family:"Outfit",sans-serif;font-weight:500;font-size:13px;line-height:24px}
.quote p{font-family:"Outfit",sans-serif;font-size:17px;line-height:25px;margin-top:20px}
.quote .who{margin-top:22px;font-size:9px;display:flex;gap:40px}
/* footer */
.foot{top:3672px;height:269px;background:var(--soft)}
.foot .col{position:absolute;top:48px;font-size:10px;color:#555}
.foot .col h4{font-size:13px;color:var(--ink);margin-bottom:18px}
.foot .col li{list-style:none;margin-bottom:10px}
.flogo{font-family:"Outfit",sans-serif;font-weight:700;font-size:20px;color:var(--ink);display:flex;align-items:center;gap:8px}
.flogo i{width:12px;height:12px;background:var(--ink)}
.news{width:206px;height:32px;background:#fff;border-radius:20px;display:flex;align-items:center;padding:0 6px 0 14px;font-size:9px;color:#999}
.news span{margin-left:auto;width:24px;height:24px;border-radius:50%;background:var(--purple)}
.socials{display:flex;gap:8px;margin-top:14px}
.socials i{width:20px;height:20px;background:#fff;border:1px solid var(--line)}
.socials i.on{background:var(--purple)}
.copy{position:absolute;left:0;width:1200px;top:248px;text-align:center;font-size:9px;color:#555}
</style>
</head>
<body>

<div class="wrap topbar"><span>☎ 044 512 40 73</span><span>✉ info@tuetenwerk.ch</span><span class="right">Produktion &amp; Versand Aus Der Schweiz</span></div>

<div class="logo">Tütenwerk</div>
<header class="wrap nav">
  <nav class="menu"><span>Home</span><span>Produkte</span><span>So Funktioniert's</span><span>Über Uns</span><span>Kontakt</span></nav>
  <div class="acts">
    <span class="pill fill">Design Hochladen</span>
    <span class="pill out">Jetzt Gestalten</span>
    <svg width="14" height="14" viewBox="0 0 14 14" fill="none" stroke="#15131c" stroke-width="1.3"><circle cx="7" cy="4.5" r="3"/><path d="M1.5 13c.8-3 3-4.5 5.5-4.5s4.7 1.5 5.5 4.5"/></svg>
    <svg width="15" height="14" viewBox="0 0 15 14" fill="none" stroke="#15131c" stroke-width="1.3"><path d="M1 1h2l2 8h7l2-6H4"/><circle cx="6" cy="12" r="1"/><circle cx="11" cy="12" r="1"/></svg>
  </div>
</header>

<section class="wrap hero">
  <div class="ph hero-bg" role="img" aria-label="Hintergrundfoto: bedruckte Papierbeutel, Laterne und Stallplakette auf Holztisch"></div>
  <div class="ph hero-prod" role="img" aria-label="Produktfoto: Papierbeutel, Laterne mit Pferdemotiv und Hundemarke"></div>
  <svg class="hero-blob" width="520" height="440" viewBox="0 0 520 440">
    <defs><linearGradient id="hb" x1="0" y1="0" x2="1" y2="1"><stop offset="0" stop-color="#ff3d8b"/><stop offset=".55" stop-color="#c13cf0"/><stop offset="1" stop-color="#6d44f2"/></linearGradient></defs>
    <path d="M140 40 C260 -10 420 20 470 110 C520 200 480 330 380 370 C290 405 200 330 130 320 C50 310 10 230 30 150 C45 95 80 65 140 40Z" fill="url(#hb)" opacity=".92"/>
  </svg>
  <div class="hero-txt">
    <span class="tag">Individuell Bedruckt</span>
    <h1>Deine Idee.<br>Dein Produkt.</h1>
    <p>Papierbeutel, Stallplaketten, Laternen Und Individuelle Produkte<br>Einfach Online Gestalten Und Bestellen.</p>
    <div class="hero-btns"><span>Jetzt Gestalten</span><span>Design Hochladen</span></div>
  </div>
  <div class="notch">Scroll Down</div>
</section>

<div class="wrap features">
  <div class="feat"><svg width="28" height="22" viewBox="0 0 28 22"><rect x="2" y="5" width="15" height="11" fill="#ff3d8b"/><path d="M17 8h5l4 4v4h-9z" fill="#e33"/><circle cx="7" cy="17" r="3" fill="#333"/><circle cx="21" cy="17" r="3" fill="#333"/></svg><div><b>Free Shipping</b><small>Free shipping over CHF 150</small></div></div>
  <div class="feat"><svg width="26" height="22" viewBox="0 0 26 22"><rect x="2" y="4" width="20" height="14" rx="2" fill="#38a8e0"/><rect x="2" y="8" width="20" height="3" fill="#f5b400"/></svg><div><b>Secure Payment</b><small>Safe &amp; secure checkout</small></div></div>
  <div class="feat"><svg width="24" height="24" viewBox="0 0 24 24"><circle cx="12" cy="8" r="5" fill="#f5a623"/><rect x="4" y="14" width="16" height="8" rx="4" fill="#ff5a3c"/></svg><div><b>Fast Production</b><small>Quick production &amp; delivery</small></div></div>
  <div class="feat"><svg width="24" height="26" viewBox="0 0 24 26"><circle cx="12" cy="9" r="7" fill="#7b3ff2"/><path d="M7 15l-2 9 7-3 7 3-2-9" fill="#f5b400"/></svg><div><b>Ch Swiss Quality</b><small>Made &amp; printed in Switzerland</small></div></div>
</div>

<section class="wrap serv">
  <div class="ph img1" role="img" aria-label="Foto: bedruckter Papierbeutel mit Tiermotiv und Hundemarke"></div>
  <div class="ph img2" role="img" aria-label="Foto: Papierbeutel und ovale Stallplakette vor Laterne"></div>
  <div class="blob"></div>
  <div class="txt">
    <span class="tag">Unsere Leistungen</span>
    <h2><span class="uline">Individuelle</span> Drucklösungen<br>Für Privat &amp; Unternehmen</h2>
    <p>Wir bedrucken Papierbeutel, Taschen, Stallplaketten, Laternen, Schilder und vieles mehr. Einfach Design hochladen oder direkt online gestalten.</p>
    <div class="check"><i></i>Eigenes Design hochladen</div>
    <div class="check"><i></i>Kleine &amp; grosse Auflagen</div>
    <div class="check"><i></i>Produktion in der Schweiz</div>
    <div class="check"><i></i>Individuelle Sonderanfertigungen</div>
    <span class="btn-grad" style="margin-top:14px;padding:9px 16px;font-size:9px">Read More</span>
    <div class="swiss"><b>CH</b>Swiss Made</div>
  </div>
  <div class="dot" style="left:1088px;top:168px;width:22px;height:22px;background:radial-gradient(#a5ecf7,#52c8e0)"></div>
</section>

<section class="wrap prod">
  <span class="tag">Produktbereiche</span>
  <h2>Unsere <span class="uline">Produkt</span>bereiche</h2>
  <div class="cards">
    <div class="card"><div class="ph" role="img" aria-label="Foto: brauner Papierbeutel mit Etikett und Kaffeebohnen" style="background:linear-gradient(160deg,#dfe0e2,#b08a63 55%,#e3e0dc)"></div><h3>Papierbeutel &amp; Taschen</h3><p>Nachhaltige Papierbeutel individuell bedruckt.</p><a>Jetzt Gestalten</a></div>
    <div class="card" style="box-shadow:0 10px 30px rgba(30,20,60,.12)"><div class="ph" role="img" aria-label="Foto: gravierte Holzplakette an einer Stalltür" style="background:linear-gradient(160deg,#7a5a3a,#3b2a1c 55%,#8a6a48)"></div><h3>Stallplaketten</h3><p>Personalisierte Stall- und Turnierplaketten.</p><a>Jetzt Gestalten</a></div>
    <div class="card"><div class="ph" role="img" aria-label="Foto: weisse Laterne mit Tiermotiv vor grüner Hecke" style="background:linear-gradient(160deg,#3f6b2a,#e9e6df 50%,#4a7a30)"></div><h3>Diverses</h3><p>Laternen, Hundemarken, Schilder und mehr.</p><a>Mehr Entdecken</a></div>
  </div>
</section>

<section class="wrap steps">
  <span class="tag">So Funktioniert's</span>
  <h2>In <span class="uline">Wenigen</span> Schritten<br>Zum Fertigen Produkt</h2>
  <div class="steprow">
    <div class="step"><svg width="40" height="40" viewBox="0 0 40 40"><rect x="2" y="2" width="36" height="36" rx="8" fill="#1f7ae0"/><path d="M20 10v14M14 16l6-6 6 6M11 24v6h18v-6" stroke="#fff" stroke-width="2.5" fill="none"/></svg>Design Hochladen</div>
    <div class="step"><svg width="40" height="44" viewBox="0 0 40 44"><path d="M20 6l8 14-8 18-8-18z" fill="#f5b400"/><circle cx="20" cy="22" r="3" fill="#fff"/><path d="M4 8h32" stroke="#7b3ff2" stroke-width="1.5"/><rect x="2" y="6" width="4" height="4" fill="#7b3ff2"/><rect x="34" y="6" width="4" height="4" fill="#7b3ff2"/></svg>Produkt Gestalten</div>
    <div class="step"><svg width="40" height="40" viewBox="0 0 40 40"><path d="M4 20c5-8 11-11 16-11s11 3 16 11c-5 8-11 11-16 11S9 28 4 20z" fill="#f5b400"/><circle cx="20" cy="20" r="7" fill="#1f7ae0"/><circle cx="20" cy="20" r="3" fill="#15131c"/></svg>Vorschau Prüfen</div>
    <div class="step"><svg width="40" height="42" viewBox="0 0 40 42"><path d="M6 8h4l4 20h18l3-14H12" fill="none" stroke="#ff3d8b" stroke-width="3"/><rect x="16" y="6" width="8" height="10" fill="#f5b400"/><rect x="24" y="2" width="8" height="14" fill="#7b3ff2"/><circle cx="16" cy="34" r="3" fill="#333"/><circle cx="30" cy="34" r="3" fill="#333"/></svg>Bestellen &amp; Erhalten</div>
  </div>
</section>

<section class="wrap why">
  <div class="txt">
    <span class="tag">Warum Wir</span>
    <h2><span class="uline">Warum</span> Kunden Uns Vertrauen</h2>
    <p>Hochwertige Materialien, individuelle Gestaltung und zuverlässige Produktion aus der Schweiz. Wir fertigen personalisierte Produkte mit viel Liebe zum Detail für Privatkunden, Unternehmen und besondere Anlässe.</p>
    <div class="grid2">
      <div class="check"><i></i>Eigenes Design einfach hochladen</div><div class="check"><i></i>Produktion &amp; Versand aus der Schweiz</div>
      <div class="check"><i></i>Produkte online individuell gestalten</div><div class="check"><i></i>Hochwertige Materialien &amp; sauberer Druck</div>
      <div class="check"><i></i>Kleine &amp; grosse Auflagen möglich</div><div class="check"><i></i>Für Privatkunden &amp; Unternehmen geeignet</div>
    </div>
    <span class="btn-grad" style="margin-top:16px;padding:12px 18px;font-size:9px">Jetzt Produkt Gestalten</span>
  </div>
  <svg style="position:absolute;left:690px;top:0" width="360" height="400"><path d="M20 20 C150 -10 320 0 340 120 C360 240 300 360 180 380 C60 400 0 300 10 180Z" fill="#f3ecfb"/></svg>
  <div class="ph c1" role="img" aria-label="Foto: Druckmaschine in der Produktion"></div>
  <div class="ph c2" role="img" aria-label="Foto: 3D-Drucker mit orangem Druckkopf"></div>
  <div class="ph c3" role="img" aria-label="Foto: Hand mit Handschuh bei der Gravur"></div>
  <div class="dot" style="left:692px;top:275px;width:8px;height:8px;background:#f59a23"></div>
  <div class="dot" style="left:950px;top:310px;width:36px;height:36px;background:radial-gradient(circle at 30% 30%,#fff,#e7d6f7)"></div>
</section>

<section class="wrap gal">
  <svg style="position:absolute;left:0;top:-80px" width="80" height="180"><path d="M0 0 C60 20 90 100 40 180 L0 180Z" fill="#fde3ef"/></svg>
  <h3>Entdecke eine Auswahl unserer personalisierten Druck- und Laserprodukte für<br>Privatkunden, Unternehmen und besondere Anlässe.</h3>
  <div class="ph" role="img" aria-label="Foto: Laterne mit Stallplakette Reitmotiv" style="left:0;top:96px;width:176px;height:352px;background:linear-gradient(160deg,#d8c7b3,#f0ece6 50%,#b89a7a)"></div>
  <div class="ph" role="img" aria-label="Foto: runde Hundemarke mit Namen" style="left:216px;top:168px;width:202px;height:214px;background:radial-gradient(circle at 50% 55%,#e4e4e4,#a98460 60%,#6e4f33)"></div>
  <div class="ph" role="img" aria-label="Foto: Papierbeutel mit Tiermotiv" style="left:472px;top:102px;width:257px;height:342px;background:linear-gradient(160deg,#d9c8b0,#c29870 55%,#e4d8c8)"></div>
  <div class="ph" role="img" aria-label="Foto: ovale Stallplakette mit Pferdeköpfen" style="left:780px;top:156px;width:202px;height:214px;background:linear-gradient(160deg,#5e7a45,#efeeea 45%,#d8cfc3)"></div>
  <div class="ph" role="img" aria-label="Foto: beleuchtete Laterne mit Schriftzug" style="left:1024px;top:102px;width:176px;height:342px;background:linear-gradient(160deg,#d7c6b0,#f2b85a 50%,#a98a6a)"></div>
  <div class="btn">Alle Produkte Entdecken <span style="color:var(--pink);margin-left:6px">➚</span></div>
</section>

<section class="wrap test">
  <span class="tag">Kundenbewertungen</span>
  <h2>Was <span class="uline">Unsere</span> Kunden Sagen</h2>
  <div class="arrows">
    <span style="background:#fff;border:1px solid var(--line)"><svg width="10" height="10"><path d="M7 1L3 5l4 4" stroke="#15131c" stroke-width="1.5" fill="none"/></svg></span>
    <span style="background:var(--orange)"><svg width="10" height="10"><path d="M3 1l4 4-4 4" stroke="#fff" stroke-width="1.5" fill="none"/></svg></span>
  </div>
  <div class="avatar" role="img" aria-label="Kundenfoto klein" style="left:76px;top:110px;width:40px;height:40px;background:#d8cbc0"></div>
  <div class="portrait" role="img" aria-label="Porträtfoto einer zufriedenen Kundin"></div>
  <svg style="position:absolute;left:215px;top:370px" width="100" height="30"><path d="M2 2 C20 25 60 28 90 12" stroke="#ff3d8b" stroke-dasharray="3 4" fill="none"/></svg>
  <div class="avatar" role="img" aria-label="Kundenfoto klein" style="left:1110px;top:323px;width:44px;height:44px;background:#d6c4b4"></div>
  <div class="quote">
    <div class="head"><svg width="36" height="28" viewBox="0 0 36 28"><path d="M2 28V14C2 6 6 2 14 0v6c-4 1-5 4-5 8h5v14zM20 28V14c0-8 4-12 12-14v6c-4 1-5 4-5 8h5v14z" fill="#7b3ff2"/></svg><b>I Really Enjoyed<br>Working With Matteo</b></div>
    <p>“Sehr hochwertige Druckqualität und ein wirklich einfacher Bestellprozess. Unsere Stallplaketten und Papierbeutel sehen genau so aus, wie wir es uns vorgestellt haben. Die Verarbeitung ist hochwertig, der Druck gestochen scharf und die Lieferung kam schneller als erwartet. Man merkt sofort, dass hier mit viel Liebe zum Detail gearbeitet wird.”</p>
    <div class="who"><b>SANDRA M.</b><span>Privatkundin Schweiz</span></div>
  </div>
</section>

<footer class="wrap foot">
  <div class="col" style="left:122px;top:52px;width:200px">
    <div class="flogo"><i></i>Tütenwerk</div>
    <p style="margin-top:22px;line-height:18px">Individuelle Druck- und Laserprodukte für Privatkunden, Unternehmen und besondere Anlässe.</p>
    <p style="margin-top:22px;color:var(--ink)">☎ 044 512 40 73</p>
    <p style="margin-top:8px;color:var(--ink)">✉ info@tuetenwerk.ch</p>
  </div>
  <div class="col" style="left:452px"><h4>Produkte</h4><ul><li>Papierbeutel</li><li>Stallplaketten</li><li>Laternen</li><li>Hundemarken</li><li>Alle Produkte</li></ul></div>
  <div class="col" style="left:653px"><h4>Informationen</h4><ul><li>So funktioniert's</li><li>Über uns</li><li>FAQ</li><li>Datenschutz</li><li>Kontakt</li></ul></div>
  <div class="col" style="left:872px"><h4>Newsletter</h4><div class="news">E-Mail eingeben<span></span></div>
    <div class="socials"><i></i><i class="on"></i><i></i><i></i></div></div>
  <div class="copy">© 2026 Pfotenwerk Shop. Alle Rechte vorbehalten.</div>
</footer>

</body>
</html>
```